Graphic- Educational Visual

Brisko Dog Training has created an educational tool to help its students understand and prioritize some key concepts in their dog training.

We are requesting a visual of this tool be designed.

Name/title of tool (to be included in graphic): The Brisko Pathway
Description: Funnel (inverted pyramid).

From top to bottom, the levels are called:

Connect
Develop
Progress
Refine

The diagram should also include a cycle around it to, to represent that one is always moving through the levels.

Business colours are included below to make sure the funnel's colours complement the website colours or at least don't clash:

#0AA1C7 Blue and #7FC31B Green
Purple as a secondary colour -75279C

For reference, business logo is attached.

Dog Training

```html
<!DOCTYPE html>
<html lang="en">
<head>
<meta charset="utf-8">
<title>The Brisko Pathway</title>
<link rel="stylesheet" href="https://fonts.googleapis.com/css2?family=Mulish:wght@700;800&display=swap">
<style>
  :root {
    --blue: #19a1c8;
    --green: #7fc242;
    --charcoal: #414141;
    --white: #ffffff;
    --canvas: #ffffff;
  }
  html, body {
    margin: 0;
    padding: 0;
    width: 1200px;
    height: 1200px;
    overflow: hidden;
    background: var(--canvas);
  }
  .pathway {
    position: relative;
    width: 1200px;
    height: 1200px;
  }
  .pathway__title {
    position: absolute;
    top: 168px;
    left: 0;
    width: 1200px;
    margin: 0;
    text-align: center;
    font-family: "Mulish", sans-serif;
    font-weight: 800;
    font-size: 56px;
    letter-spacing: -0.5px;
    color: var(--blue);
    line-height: 1;
  }
  .pathway__diagram {
    position: absolute;
    inset: 0;
  }
  .level-label {
    font-family: "Mulish", sans-serif;
    font-weight: 800;
    font-size: 27px;
    fill: var(--white);
  }
  .level-icon {
    fill: none;
    stroke: var(--white);
    stroke-width: 2.6;
    stroke-linecap: round;
    stroke-linejoin: round;
  }
  .level-icon--solid { fill: var(--white); stroke: none; }
  .band--blue { fill: var(--blue); }
  .band--green { fill: var(--green); }
  .ribbon { fill: var(--charcoal); }
  .cycle-arc { fill: none; stroke-width: 42; }
  .cycle-head--green { fill: var(--green); }
  .cycle-head--blue { fill: var(--blue); }
  .cycle-head--charcoal { fill: var(--charcoal); }
</style>
</head>
<body>
<main class="pathway">
  <h1 class="pathway__title">The Brisko Pathway</h1>

  <svg class="pathway__diagram" width="1200" height="1200" viewBox="0 0 1200 1200" xmlns="http://www.w3.org/2000/svg">
    <defs>
      <linearGradient id="fade-green" gradientUnits="userSpaceOnUse" x1="0" y1="800" x2="0" y2="610">
        <stop offset="0" stop-color="var(--green)" stop-opacity="0"/>
        <stop offset="1" stop-color="var(--green)"/>
      </linearGradient>
      <linearGradient id="fade-blue" gradientUnits="userSpaceOnUse" x1="645" y1="325" x2="800" y2="425">
        <stop offset="0" stop-color="var(--blue)" stop-opacity="0"/>
        <stop offset="1" stop-color="var(--blue)"/>
      </linearGradient>
      <linearGradient id="fade-charcoal" gradientUnits="userSpaceOnUse" x1="885" y1="890" x2="720" y2="1010">
        <stop offset="0" stop-color="var(--charcoal)" stop-opacity="0"/>
        <stop offset="1" stop-color="var(--charcoal)"/>
      </linearGradient>
    </defs>

    <!-- Cycle ring -->
    <g class="cycle">
      <path class="cycle-arc" stroke="url(#fade-green)" d="M253 777 A359 359 0 0 1 600 325"/>
      <polygon class="cycle-head--green" points="600,274 600,376 652,325"/>

      <path class="cycle-arc" stroke="url(#fade-blue)" d="M693 337 A359 359 0 0 1 911 863.5"/>
      <polygon class="cycle-head--blue" points="955,889 867,838 886,910"/>

      <path class="cycle-arc" stroke="url(#fade-charcoal)" d="M875 915 A359 359 0 0 1 280 847"/>
      <polygon class="cycle-head--charcoal" points="236,870 326,824 256,800"/>
    </g>

    <!-- Funnel -->
    <g class="funnel">
      <polygon class="ribbon" points="626,584 836,584 626,645 389,645"/>
      <polygon class="ribbon" points="624,706 782,706 626,767 442,767"/>
      <polygon class="ribbon" points="626,829 730,829 626,890 496,890"/>

      <g class="level level--connect">
        <polygon class="band--blue" points="334,522 862,522 836,584 362,584"/>
        <g class="level-icon" transform="translate(538,553) rotate(-45)">
          <rect x="-16" y="-6" width="17" height="12" rx="6"/>
          <rect x="-1" y="-6" width="17" height="12" rx="6"/>
        </g>
        <text class="level-label" x="570" y="563">Connect</text>
      </g>

      <g class="level level--develop">
        <polygon class="band--green" points="389,645 810,645 782,706 414,706"/>
        <path class="level-icon--solid" d="M541 690 L527 676 A8.5 8.5 0 0 1 541 664 A8.5 8.5 0 0 1 555 676 Z"/>
        <text class="level-label" x="573" y="686">Develop</text>
      </g>

      <g class="level level--progress">
        <polygon class="band--blue" points="442,767 756,767 730,829 468,829"/>
        <polyline class="level-icon" points="529,810 537,798 541,804 550,789"/>
        <polygon class="level-icon--solid" points="544,788 553,784 552,794"/>
        <text class="level-label" x="567" y="808">Progress</text>
      </g>

      <g class="level level--refine">
        <polygon class="band--green" points="496,890 702,890 677,951 522,951"/>
        <g class="level-icon">
          <circle cx="549" cy="927" r="6"/>
          <circle cx="549" cy="927" r="2"/>
          <circle cx="561" cy="913" r="4.5"/>
          <circle cx="561" cy="913" r="1.5"/>
        </g>
        <text class="level-label" x="579" y="932">Refine</text>
      </g>
    </g>
  </svg>
</main>
</body>
</html>
```